Card Design for my dog training business Brightpaw Obedience

Need a business card design for my dog training business with my new logo. Want the card to come off professional yet fun. Want it to be very eye catchy as well. I normally have these at vet clinics, pet stores, and groomers. so need it to look better than my competitors.
Target Market(s)
dog owners
Industry/Entity Type
Dog Training
Contact Information for Business Card
needs logo, my name and info
Font styles to use
Serif
Colors
0255a3
ffffff
ec1f27
000000
333333
fbfbfb
Requirements
Must have
- Brightpaw Obedience
- Felix Orland
- 415 903 2276
- info@brightpawobedience.example
- www.brightpawobedience.example

```html
<!DOCTYPE html>
<html lang="en">
<head>
<meta charset="utf-8">
<title>Brightpaw Obedience – Business Card</title>
<link href="https://fonts.googleapis.com/css2?family=EB+Garamond:ital@1&family=Noto+Serif:wght@400&display=swap" rel="stylesheet">
<style>
  :root {
    --stage: #cccccc;
    --brand-blue: #0255a3;
    --bright-blue: #0090dc;
    --band-blue: #0094de;
    --brand-red: #ec1f27;
    --paper: #fbfbfb;
    --white: #ffffff;
    --ink: #333333;
  }
  * { margin: 0; padding: 0; box-sizing: border-box; }
  html, body {
    width: 1200px; height: 992px; overflow: hidden;
    background: var(--stage);
  }
  body { position: relative; font-family: "Noto Serif", serif; }

  .card {
    position: absolute; top: 201px;
    width: 357px; height: 591px; overflow: hidden;
  }
  .card--front {
    left: 209px;
    background: linear-gradient(160deg, var(--bright-blue) 0%, #0272c0 45%, var(--brand-blue) 100%);
  }
  .card--back {
    left: 634px; top: 200px;
    background: var(--paper);
    box-shadow: 0 0 0 1px #e2c9c9;
  }

  .brand-name {
    position: absolute; left: 0; right: 0;
    text-align: center;
    font-family: "Noto Serif", serif;
    font-weight: 400;
    line-height: 1.15;
  }
  .card--front .brand-name { top: 268px; font-size: 30px; color: var(--white); }
  .card--back .brand-name { top: 140px; font-size: 26px; color: var(--brand-blue); }

  .brand-dot {
    position: absolute; left: 50%; transform: translateX(-50%);
    border-radius: 50%;
  }
  .card--front .brand-dot { top: 206px; width: 40px; height: 40px; background: var(--white); }
  .card--back .brand-dot { top: 92px; width: 34px; height: 34px; background: var(--brand-blue); }

  .tagline {
    position: absolute; left: 0; right: 0;
    text-align: center;
    font-family: "EB Garamond", serif;
    font-style: italic;
    font-size: 14.5px;
    color: var(--white);
  }
  .card--front .tagline { top: 532px; }

  .wave { position: absolute; left: 0; top: 0; width: 357px; height: 591px; }

  .person { position: absolute; left: 0; right: 0; top: 340px; text-align: center; color: var(--white); }
  .person__name { font-size: 24px; letter-spacing: 0.2px; }
  .person__role { font-size: 14.5px; margin-top: 6px; }

  .divider {
    position: absolute; top: 437px; left: 44px; width: 270px; height: 14px;
    display: flex; align-items: center; justify-content: center; gap: 8px;
  }
  .divider__line { flex: 1; height: 2px; background: linear-gradient(90deg, transparent, var(--white)); }
  .divider__line--right { background: linear-gradient(90deg, var(--white), transparent); }
  .divider__icons { display: flex; gap: 10px; padding: 0 4px; }

  .contact {
    position: absolute; left: 0; right: 0; top: 461px;
    list-style: none; text-align: center;
    color: var(--white); font-size: 14.5px; line-height: 21px;
  }

  .tag-band {
    position: absolute; left: 0; right: 0; bottom: 0; height: 33px;
    background: var(--band-blue);
  }
  .tag-band .tagline { top: 7px; }
</style>
</head>
<body>

  <section class="card card--front" aria-label="Card front">
    <span class="brand-dot"></span>
    <div class="brand-name">Brightpaw<br>Obedience</div>
    <p class="tagline">“Teaching good manners one happy dog at a time.”</p>
  </section>

  <section class="card card--back" aria-label="Card back">
    <span class="brand-dot"></span>
    <div class="brand-name">Brightpaw<br>Obedience</div>

    <svg class="wave" viewBox="0 0 357 591" aria-hidden="true">
      <path d="M0 240 Q175 344 357 240 L357 591 L0 591 Z" fill="var(--brand-red)"/>
      <path d="M0 246 Q175 336 357 264 L357 591 L0 591 Z" fill="var(--brand-blue)"/>
    </svg>

    <div class="person">
      <div class="person__name">Felix Orland</div>
      <div class="person__role">Dog Trainer</div>
    </div>

    <div class="divider">
      <span class="divider__line"></span>
      <span class="divider__icons">
        <svg width="13" height="11" viewBox="0 0 13 11" aria-label="Phone"><path d="M1 4 Q6.5 -1 12 4 L10 5 L9 3.5 Q6.5 2.5 4 3.5 L3 5 Z M3 6 H10 L11 10 H2 Z" fill="#fff"/></svg>
        <svg width="13" height="11" viewBox="0 0 13 11" aria-label="Email"><rect x="0.5" y="1.5" width="12" height="8" fill="#fff"/><path d="M0.5 1.5 L6.5 6 L12.5 1.5" stroke="var(--brand-blue)" fill="none"/></svg>
        <svg width="12" height="12" viewBox="0 0 12 12" aria-label="Website"><circle cx="6" cy="6" r="5.2" fill="#fff"/><g stroke="var(--brand-blue)" stroke-width="0.8" fill="none"><ellipse cx="6" cy="6" rx="2.2" ry="5.2"/><path d="M0.8 6 H11.2 M1.6 3.5 H10.4 M1.6 8.5 H10.4"/></g></svg>
      </span>
      <span class="divider__line divider__line--right"></span>
    </div>

    <ul class="contact">
      <li>415 903 2276</li>
      <li>info@brightpawobedience.example</li>
      <li>www.brightpawobedience.example</li>
    </ul>

    <div class="tag-band">
      <p class="tagline">“Teaching good manners one happy dog at a time.”</p>
    </div>
  </section>

</body>
</html>
```